SitePress Direct-Booking Website for Bend, Oregon Vacation Rental — $750 Budget
Project Overview

We are looking for a talented SitePress designer/developer to create a clean, professional and inviting direct-booking website for Birch Lantern Retreat, an established short-term vacation rental in Bend, Oregon.

The property is currently successfully listed on Staynest and Hoplo. Our Staynest property has approximately a 4.98-star rating with more than 200 reviews, is an Staynest Visitor Pick, and ranks among the Top 1% of eligible homes.

Project Budget: $750

We will select the designer based on the quality of the initial concept, understanding of the property, proposed booking solution and ability to deliver a completed and functioning SitePress website.

Existing Staynest Listing

Please use our current Staynest listing as the primary reference for photographs, property details, amenities and design inspiration:

https://www.staynest-example.net/rooms/48172036

Original high-resolution photographs and additional property information will be provided to the selected designer.

Design Direction

We want the website to feel:

Upscale but comfortable
Warm and welcoming
Clean and uncluttered
Pacific Northwest / Central Oregon
Professional rather than corporate
Highly visual with large property photographs
Easy to navigate
Excellent on phones, tablets and desktop computers

We welcome creativity and want designers to show us their vision for the property rather than simply copying our Staynest listing.

The website should immediately communicate that Birch Lantern Retreat is a highly rated vacation rental in an excellent Bend location.

Key Property Features
3 bedrooms
2 bathrooms
Sleeps up to 6 guests
Pet friendly
Approximately a 5-minute walk to Bend's Tannery Row Quarter
Near restaurants, shopping and Larkspur Fields Pavilion
Private fenced backyard
Covered outdoor area
Off-street driveway parking
Fireplace
Well-equipped kitchen
Staynest Prime Keeper
Staynest Visitor Pick
Top 1% of eligible Staynest homes
Approximately 4.98 stars with 200+ guest reviews

Our location, guest reviews, cleanliness, comfort, backyard, pet-friendly accommodations and walkability should be major selling points throughout the website.

Website Structure

We anticipate approximately 6–7 pages:

Home

Large hero photograph with a strong opening message and prominent BOOK DIRECT and CHECK AVAILABILITY buttons.

The home page should quickly communicate:

BIRCH LANTERN RETREAT — BEND, OREGON

3 Bedrooms | 2 Baths | Sleeps 6 | Pet Friendly | Walk to Tannery Row

Our exceptional guest rating and Staynest history should also be prominently featured.

The House

Bedrooms, bathrooms, kitchen, living areas, backyard and major amenities.

Photo Gallery

Large, attractive and fast-loading photographs with an easy-to-use mobile gallery.

Location / Explore Bend

Tannery Row Quarter, Larkspur Fields Pavilion, Deschutes River, restaurants, breweries, shopping, downtown Bend and nearby outdoor recreation.

Guest Reviews

Selected guest reviews and prominent presentation of our strong Staynest reputation.

Availability & Book Direct

A simple and professional direct-booking experience.

Contact / FAQ

Contact information plus common questions regarding pets, parking, check-in/check-out, cancellations and other policies.

IMPORTANT — Direct Booking & Credit Card Requirements

We want guests to be able to book directly through the website without having to contact us first.

The website should use a proven SitePress vacation-rental booking plugin or system rather than a custom-built reservation/payment system.

Guests should be able to:

Select arrival and departure dates
See available dates
Enter number of guests
See nightly charges
See cleaning fees
See applicable lodging taxes and other charges
See the complete reservation total before paying
Enter guest/contact information
Pay securely by credit or debit card
Receive an automatic reservation confirmation

Paywell is our preferred credit-card processor.

Credit-card information must be processed securely through Paywell or another established payment processor. Credit-card information should NOT be stored directly on our SitePress website.

Staynest & Hoplo Calendar Synchronization

This is very important.

The direct-booking calendar must synchronize with our existing Staynest and Hoplo calendars to reduce the possibility of double bookings.

For this single-property website, we prefer a simple solution using Staynest/Hoplo calendar or iCal synchronization rather than an expensive monthly channel-management service, if practical.

The designer should clearly identify the booking plugin/system they propose using.

IMPORTANT — Tell Us Your Proposed Booking Solution

As part of your submission, please tell us:

Which SitePress booking plugin/system you recommend.
Whether it synchronizes availability with Staynest and Hoplo.
Whether it integrates directly with Paywell.
The initial cost of the plugin/software.
Any annual or monthly fees.
Whether any additional paid software or services will be required.

We strongly prefer a solution with little or no ongoing monthly software expense.

We do not want to select a designer and later discover that the proposed booking system requires an expensive monthly subscription.

SitePress & Technical Requirements

The completed project should include:

Fully functioning SitePress website
Responsive desktop/tablet/mobile design
Fast-loading pages
Optimized photographs
SSL/HTTPS compatibility
Direct-booking functionality
Paywell payment integration
Staynest calendar synchronization
Hoplo calendar synchronization
Automatic booking confirmations
Cleaning fee and lodging-tax calculations
Contact form
Vizor Maps/location integration
Basic spam/security protection
Vizor Metrics capability
Basic SEO setup
Search-engine submission capability
Easy owner editing of text, rates and photographs
Search Engine Optimization

The website should be structured for Vizor and other search engines.

Important search themes include:

Bend Oregon vacation rental
Bend Oregon vacation home
Tannery Row Quarter vacation rental
Vacation rental near Tannery Row Bend
Bend Oregon pet-friendly vacation rental
Bend vacation rental near Larkspur Fields Pavilion
Bend Oregon direct booking vacation rental

We are not expecting an extensive ongoing SEO campaign for the $750 project. We do expect proper page titles, descriptions, headings, image optimization and a good technical foundation for future SEO.

Ownership

Upon completion and final payment:

We own the completed SitePress website.
We receive full SitePress administrator access.
We control the domain and hosting accounts.
We own all custom design files created for the project.
All necessary login credentials are provided to us.
The website can be moved to another SitePress hosting provider in the future.
There should be no proprietary dependency on the developer after completion.
What We Want From Contestants

Please review our Staynest listing before submitting your concept.

We are particularly interested in seeing an initial homepage concept showing how you would present:

Birch Lantern Retreat
The Bend / Tannery Row location
Our photography
Our exceptional guest reviews and ratings
The Book Direct message
The availability/booking call-to-action

We will provide feedback on the concepts we like and work with the selected designer to refine and complete the website.

Our Goal

Our objective is straightforward:

Create a beautiful, trustworthy and easy-to-use website that encourages guests to book Birch Lantern Retreat directly with us.

The website will complement—not replace—our existing Staynest and Hoplo listings.

We want repeat guests and new customers to have an easy way to find the property, check availability and book directly while receiving the same professional experience they expect from a major vacation-rental platform.

Target Market(s)

Consumers looking to to travel to Mexico for vacation. Family or couples

Industry/Entity Type

Short term vacation rental industry

Coding

Coded - Design and coding required

Number of Pages Required

5+ page

Requirements
Must have
• Capabilities to accept credit card payments and link to other rental property sites calendars such as HOPLO and Staynset
Nice to have
• Option for best plugins for property rental

```html
<!DOCTYPE html>
<html lang="en">
<head>
<meta charset="utf-8">
<title>Birch Lantern Retreat — Bend, Oregon Vacation Rental</title>
<link href="https://fonts.googleapis.com/css2?family=Playfair+Display:wght@400;500;600&family=Poppins:wght@400;500;600&family=Playball&display=swap" rel="stylesheet">
<style>
:root{
  --maroon:#7b0f15;
  --maroon-dark:#5e0a0f;
  --ink:#1b1b1b;
  --muted:#555;
  --cream:#f5f2ec;
  --line:#e3ddd4;
  --gold:#f4b400;
  --white:#fff;
  --footer:#151515;
}
*{box-sizing:border-box;margin:0;padding:0}
html,body{width:1200px;height:4998px;overflow:hidden}
body{font-family:"Poppins",sans-serif;color:var(--ink);background:var(--white);position:relative}
.abs{position:absolute}
section,header,footer{position:absolute;left:0;width:1200px}
.serif{font-family:"Playfair Display",serif}
.script{font-family:"Playball",cursive;color:var(--maroon)}
.btn{position:absolute;display:flex;align-items:center;justify-content:center;gap:8px;font-size:10px;font-weight:600;letter-spacing:.5px;border-radius:4px;text-transform:uppercase}
.btn-maroon{background:var(--maroon);color:var(--white)}
.btn-dark{background:var(--ink);color:var(--white)}
.btn-outline{border:1px solid var(--maroon);color:var(--maroon);background:var(--white)}
.eyebrow{position:absolute;font-size:12px;font-weight:600;color:var(--maroon);letter-spacing:.5px;display:flex;align-items:center;gap:10px}
.eyebrow .rule{display:inline-block;width:40px;height:1px;background:var(--maroon)}
.photo{position:absolute;overflow:hidden}
.stars{color:var(--gold);letter-spacing:2px}

/* header */
.site-header{top:0;height:81px;background:var(--white)}
.brand-mark{left:105px;top:18px;width:46px;height:46px;border-radius:50%;background:var(--maroon)}
.brand-name{left:160px;top:20px;font-size:20px;font-weight:500;font-family:"Poppins",sans-serif}
.brand-sub{left:161px;top:47px;font-size:9px;letter-spacing:.5px}
.main-nav{left:410px;top:32px;display:flex;gap:32px;font-size:11px;font-weight:500}

/* hero */
.hero{top:81px;height:640px}
.hero-photo{left:0;top:0;width:1200px;height:636px;background:linear-gradient(90deg,#f4f2ef 0%,#eceae6 30%,#c9c5bf 55%,#a79d91 75%,#8e8375 100%)}
.hero-fade{left:0;top:0;width:700px;height:636px;background:linear-gradient(90deg,rgba(255,255,255,.95),rgba(255,255,255,.6) 70%,rgba(255,255,255,0))}
.hero-title{left:74px;top:152px;font-size:44px;font-weight:500;letter-spacing:1px}
.hero-script{left:74px;top:210px;font-size:54px}
.hero-copy{left:74px;top:292px;font-size:12px;line-height:19px;width:300px}

/* stats */
.stats-panel{left:76px;top:660px;width:1056px;height:160px;background:var(--cream);box-shadow:0 6px 20px rgba(0,0,0,.08)}
.feature-flag{left:76px;top:612px;width:520px;height:210px}
.flag-label{left:140px;top:640px;font-size:11px;color:var(--white);letter-spacing:.6px;display:flex;align-items:center;gap:10px}
.flag-label .rule{width:40px;height:1px;background:rgba(255,255,255,.6);display:inline-block}
.rating-big{left:113px;top:684px;font-size:28px;color:var(--white)}
.rating-big small{font-size:18px}
.flag-stars{left:108px;top:722px;font-size:17px}
.flag-small{font-size:11px;color:var(--white);text-align:center}
.stat{position:absolute;top:670px;width:130px;text-align:center}
.stat svg{display:block;margin:0 auto}
.stat .num{font-size:22px;font-weight:600;margin-top:14px}
.stat .lbl{font-size:11px;margin-top:4px}
.stat-div{position:absolute;top:670px;width:1px;height:120px;background:var(--line)}

/* location */
.location{top:860px;height:520px}
.h2{position:absolute;font-family:"Playfair Display",serif;font-weight:500;color:var(--ink)}
.lead{position:absolute;font-size:11px;line-height:17px;color:#333}
.place-card{position:absolute;top:180px;width:247px;height:310px;background:var(--white);border-radius:6px;box-shadow:0 4px 16px rgba(0,0,0,.1);overflow:hidden}
.place-card .pic{height:190px}
.place-card .tag{position:absolute;right:12px;top:16px;background:var(--white);border-radius:12px;font-size:9px;padding:3px 9px;color:var(--maroon);font-weight:500}
.place-card h3{font-size:15px;font-weight:500;margin:18px 20px 0}
.place-card p{font-size:11px;color:#444;margin:20px 20px 0;line-height:16px}

/* about */
.about{top:1400px;height:461px}
.about-photo{left:480px;top:30px;width:625px;height:342px;border-radius:10px;background:linear-gradient(180deg,#7aa2d6 0%,#b9cbe0 35%,#7f8b6b 60%,#5d6b45 100%)}
.arrow-dot{position:absolute;width:28px;height:28px;border-radius:50%;background:rgba(255,255,255,.85);display:flex;align-items:center;justify-content:center}
.book-tag{left:448px;top:300px;width:160px;height:90px;background:var(--maroon);color:var(--white);padding:22px 18px}
.dots{position:absolute;display:flex;gap:6px}
.dots span{width:9px;height:9px;border-radius:50%;background:#ccc}
.dots span.on{background:var(--maroon)}
.mountain-bg{left:0;top:330px;width:360px;height:130px;background:linear-gradient(180deg,rgba(200,200,205,0),rgba(200,200,205,.35))}

/* highlights */
.highlights{top:1861px;height:566px;background:var(--cream)}
.tabs{position:absolute;left:74px;top:160px;display:flex;gap:14px}
.tab{height:38px;border:1px solid var(--maroon);border-radius:4px;display:flex;align-items:center;gap:8px;padding:0 14px;font-size:10px;font-weight:500;color:var(--maroon);background:var(--white)}
.tab.on{background:var(--maroon);color:var(--white)}
.room{position:absolute;top:234px;height:264px;background:linear-gradient(180deg,#e9e6e1,#cfc6b8 60%,#a88a66)}

/* explore */
.explore{top:2427px;height:520px}
.explore-list{left:474px;top:68px;width:312px;height:360px;background:var(--maroon);border-radius:4px;padding:14px 28px}
.explore-item{display:flex;align-items:center;gap:16px;height:66px;border-bottom:1px solid rgba(255,255,255,.2);color:var(--white);font-size:14px;font-weight:500}
.explore-item:last-child{border-bottom:none}
.explore-item .ic{width:32px;height:32px;border-radius:50%;background:#c79a4b;flex:none}
.map{left:822px;top:136px;width:310px;height:292px;border-radius:4px;background:linear-gradient(135deg,#eef0ec,#dfe3dd);border:1px solid #ddd}

/* reviews */
.reviews{top:2947px;height:566px;background:var(--cream)}
.review{position:absolute;top:188px;height:315px;background:var(--white);border-radius:4px;box-shadow:0 4px 16px rgba(0,0,0,.06);padding:20px}
.quote{font-family:"Playfair Display",serif;font-size:64px;line-height:40px;color:#c8931e;height:40px}
.avatar{position:absolute;left:20px;top:74px;width:46px;height:46px;border-radius:50%;background:#cdbba8}
.rev-name{position:absolute;left:78px;top:76px;font-size:14px;font-weight:500}
.rev-sub{position:absolute;left:78px;top:98px;font-size:10px;color:#777}
.rev-stars{position:absolute;left:20px;top:130px;font-size:18px}
.rev-body{position:absolute;left:20px;top:168px;right:18px;font-size:11px;line-height:17px}
.rev-more{position:absolute;left:20px;bottom:22px;font-size:11px;font-weight:500;text-decoration:underline}
.score-card{left:898px;top:188px;width:234px;height:315px;text-align:center}

/* booking */
.booking{top:3513px;height:432px}
.booking-bg{left:0;top:0;width:1200px;height:432px;background:linear-gradient(180deg,#4a5060 0%,#6b5a4a 45%,#5a3e2c 75%,#3d2a1e 100%)}
.booking-bg::after{content:"";position:absolute;inset:0;background:linear-gradient(90deg,rgba(0,0,0,.45),rgba(0,0,0,.1))}
.booking-form{left:590px;top:42px;width:542px;height:362px;background:rgba(255,255,255,.94);border-radius:8px;padding:26px 32px}
.f-label{position:absolute;font-size:10px;font-weight:600}
.f-input{position:absolute;height:32px;border:1px solid #ddd;border-radius:4px;background:var(--white);font-size:10px;color:#999;display:flex;align-items:center;justify-content:space-between;padding:0 12px}
.perk{position:absolute;display:flex;align-items:center;gap:8px;color:var(--white);font-size:13px}
.perk i{width:16px;height:16px;border-radius:50%;background:var(--maroon);display:inline-block}

/* pets */
.pets{top:3945px;height:380px}
.pet-list{left:990px;top:110px;font-size:11px;line-height:16px}
.pet-list div{display:flex;gap:8px;margin-bottom:12px}
.tick{width:20px;height:20px;border-radius:50%;background:#e0a720;flex:none;display:flex;align-items:center;justify-content:center}

/* features */
.features{top:4323px;height:140px}
.feat{position:absolute;top:32px;display:flex;gap:14px;width:240px}
.feat .ic{width:62px;height:62px;border-radius:50%;background:var(--maroon);flex:none}
.feat h4{font-family:"Playfair Display",serif;font-weight:500;font-size:17px}
.feat p{font-size:9px;line-height:13px;color:#333;margin-top:4px}

/* cta band */
.cta{top:4463px;height:174px;background:var(--maroon)}
.cta-photo{left:0;top:0;width:260px;height:174px;background:linear-gradient(90deg,#8aa4c2,#7e7a6a 60%,rgba(123,15,21,1))}

/* footer */
.site-footer{top:4637px;height:361px;background:var(--footer);color:#ddd}
.f-head{position:absolute;top:66px;font-size:15px;font-weight:600;color:var(--white)}
.f-links{position:absolute;top:112px;font-size:11px;line-height:32px}
.social{position:absolute;top:190px;width:40px;height:40px;border-radius:50%;border:1px solid #555}
.contact-row{display:flex;align-items:center;gap:12px;font-size:11px;line-height:32px}
</style>
</head>
<body>

<header class="site-header">
  <div class="abs brand-mark" aria-hidden="true"></div>
  <div class="abs brand-name">Birch Lantern Retreat</div>
  <div class="abs brand-sub">BEND, OREGON</div>
  <nav class="abs main-nav"><span>HOME</span><span>THE HOUSE</span><span>GALLERY</span><span>EXPLORE BEND</span><span>REVIEWS</span><span>FAQ</span></nav>
  <div class="btn btn-maroon" style="left:933px;top:22px;width:172px;height:38px">
    <svg width="12" height="12" viewBox="0 0 12 12" fill="none" stroke="#fff"><rect x="1" y="2" width="10" height="9" rx="1"/><path d="M1 5h10M4 1v2M8 1v2"/></svg>Check availability</div>
</header>

<section class="hero">
  <div class="photo hero-photo" role="img" aria-label="Bright living room with leather sofas, ottoman and large windows"></div>
  <div class="abs hero-fade"></div>
  <div class="eyebrow" style="left:74px;top:126px"><span class="rule"></span>YOUR BEND GETAWAY NEAR TANNERY ROW QUARTER</div>
  <h1 class="abs hero-title serif">BIRCH LANTERN RETREAT</h1>
  <div class="abs hero-script">Bend, Oregon</div>
  <p class="abs hero-copy">A beautifully appointed 3-bedroom, 2-bath vacation rental in the heart of Bend.</p>
  <div class="btn btn-maroon" style="left:74px;top:354px;width:128px;height:36px">Book direct →</div>
  <div class="btn btn-dark" style="left:212px;top:354px;width:174px;height:36px">Check availability →</div>
</section>

<div class="abs stats-panel"></div>
<svg class="abs feature-flag" viewBox="0 0 520 210" aria-hidden="true"><polygon points="0,0 410,0 512,104 410,210 0,210" fill="#7b0f15"/><polygon points="410,0 512,104 410,210 418,210 520,104 418,0" fill="#c8931e"/></svg>
<div class="abs flag-label">FEATURED BIRCH LANTERN RETREAT RENTAL<span class="rule" style="width:60px"></span></div>
<div class="abs rating-big">4.98 <small>/5</small></div>
<div class="abs flag-stars stars">★★★★★</div>
<div class="abs flag-small" style="left:98px;top:752px">200+ Guest Reviews</div>
<div class="abs" style="left:300px;top:690px;width:44px;height:44px;border-radius:50%;border:2px solid rgba(255,255,255,.8)" aria-hidden="true"></div>
<div class="abs flag-small" style="left:262px;top:740px;width:120px;line-height:16px">Top 1%<br>of Eligible Homes</div>
<div class="abs" style="left:386px;top:690px;width:1px;height:70px;background:rgba(255,255,255,.3)"></div>
<div class="abs" style="left:410px;top:716px;font-size:15px;font-weight:600;color:#fff">Prime Keeper</div>
<div class="abs flag-small" style="left:410px;top:742px">Highly Rated Host</div>

<div class="stat" style="left:592px"><svg width="34" height="30" viewBox="0 0 34 30" fill="none" stroke="#7b0f15" stroke-width="2"><path d="M3 26V6M3 18h28v8M3 18v-4h28v4M7 14v-4h8v4"/></svg><div class="num">3</div><div class="lbl">BEDROOMS</div></div>
<div class="stat-div" style="left:716px"></div>
<div class="stat" style="left:720px"><svg width="34" height="30" viewBox="0 0 34 30" fill="none" stroke="#7b0f15" stroke-width="2"><path d="M3 14h28v4a8 8 0 0 1-8 8H11a8 8 0 0 1-8-8zM7 14V5a3 3 0 0 1 6 0"/></svg><div class="num">2</div><div class="lbl">BATHROOMS</div></div>
<div class="stat-div" style="left:850px"></div>
<div class="stat" style="left:852px"><svg width="34" height="30" viewBox="0 0 34 30" fill="none" stroke="#7b0f15" stroke-width="2"><path d="M4 14L17 3l13 11M8 11v16h18V11M14 27v-8h6v8"/></svg><div class="num">~1,800</div><div class="lbl">SQ FT (Approx.)</div></div>
<div class="stat-div" style="left:986px"></div>
<div class="stat" style="left:992px"><svg width="34" height="30" viewBox="0 0 34 30" fill="none" stroke="#7b0f15" stroke-width="2"><circle cx="13" cy="9" r="5"/><path d="M3 27c0-6 4-10 10-10s10 4 10 10M22 5a5 5 0 0 1 0 9M26 18c3 1 5 5 5 9"/></svg><div class="num">SLEEPS</div><div class="lbl">UP TO 6 GUESTS</div></div>

<section class="location">
  <div class="eyebrow" style="left:74px;top:28px">UNBEATABLE LOCATION<span class="rule"></span></div>
  <h2 class="h2" style="left:74px;top:48px;font-size:42px">Stay Close to Bend’s Best.</h2>
  <p class="lead" style="left:74px;top:116px;width:460px;font-size:10px">Birch Lantern Retreat puts you minutes from the Tannery Row Quarter, Deschutes River, restaurants, shopping and outdoor recreation.</p>
  <div class="btn btn-maroon" style="left:955px;top:52px;width:177px;height:38px">Check availability →</div>

  <article class="place-card" style="left:74px"><div class="pic" role="img" aria-label="Tannery Row Quarter shops and sculpture" style="background:linear-gradient(180deg,#9fb7cc,#8a6a55 60%,#6b4d3a)"></div><span class="tag">● 5 min walk</span><h3>Tannery Row Quarter</h3><p>Shops, dining &amp; entertainment</p></article>
  <article class="place-card" style="left:341px"><div class="pic" role="img" aria-label="Rafting on the Deschutes River" style="background:linear-gradient(180deg,#7f7a5a,#6e6a4c 50%,#4f6f6a)"></div><span class="tag">● 5 min walk</span><h3>Deschutes River</h3><p>Trails, water activities &amp; scenic views</p></article>
  <article class="place-card" style="left:612px"><div class="pic" role="img" aria-label="Restaurant patio with string lights" style="background:linear-gradient(180deg,#4a78b8,#8a5a3a 55%,#5a3a2a)"></div><span class="tag">● Nearby</span><h3>Restaurants &amp; Breweries</h3><p>Local favorites just minutes away</p></article>
  <article class="place-card" style="left:884px"><div class="pic" role="img" aria-label="Boutique shopping street" style="background:linear-gradient(180deg,#5d8fc0,#4e6a7a 55%,#3a4a50)"></div><span class="tag">● Nearby</span><h3>Shopping &amp; Recreation</h3><p>Shops, dining &amp; entertainment</p></article>
</section>

<section class="about">
  <div class="photo mountain-bg" role="img" aria-label="Faint mountain backdrop"></div>
  <div class="eyebrow" style="left:74px;top:52px">ABOUT THE PROPERTY<span class="rule"></span></div>
  <h2 class="h2" style="left:74px;top:76px;font-size:42px;line-height:50px">Your Perfect<br>Bend Getaway</h2>
  <p class="lead" style="left:74px;top:196px;width:345px;font-size:10px;line-height:17px">Birch Lantern Retreat is a stylish and comfortable 3-bedroom, 2-bath home in Bend, Oregon–just a 5-minute walk to the Tannery Row Quarter. Enjoy the best of Bend with easy access to restaurants, shopping, the river trails and Larkspur Fields Pavilion, then come home to a private fenced backyard and all the comforts of home.</p>
  <div class="btn btn-maroon" style="left:74px;top:298px;width:176px;height:36px">Explore the house →</div>
  <div class="photo about-photo" role="img" aria-label="Front of the grey craftsman house with flowering garden"></div>
  <div class="arrow-dot" style="left:492px;top:188px"><svg width="10" height="10" viewBox="0 0 10 10"><path d="M6 1L2 5l4 4" stroke="#333" fill="none"/></svg></div>
  <div class="arrow-dot" style="left:1056px;top:188px"><svg width="10" height="10" viewBox="0 0 10 10"><path d="M4 1l4 4-4 4" stroke="#333" fill="none"/></svg></div>
  <div class="abs book-tag"><div class="serif" style="font-size:22px">Book direct</div><div style="font-size:10px;margin-top:4px">for the best rates</div></div>
  <div class="dots" style="left:778px;top:397px"><span class="on"></span><span></span><span></span></div>
</section>

<section class="highlights">
  <h2 class="h2" style="left:76px;top:44px;font-size:44px">Property Highlights</h2>
  <p class="lead" style="left:76px;top:112px;font-size:12px">Comfortable spaces. modern amenities. true bend charm.</p>
  <div class="abs" style="left:952px;top:78px;font-size:12px;font-weight:600;color:var(--maroon);border-bottom:1px solid var(--maroon);padding-bottom:4px">VIEW FULL GALLERY →</div>
  <div class="tabs">
    <div class="tab on">LIVING ROOM</div><div class="tab">FULL KITCHEN</div><div class="tab">DINING AREA</div><div class="tab">BEDROOM</div><div class="tab">FULL BATHROOM</div><div class="tab">BACK GARDEN</div><div class="tab">PATIO</div>
  </div>
  <div class="room" style="left:74px;width:324px" role="img" aria-label="Living room with wood stove and sofas"></div>
  <div class="room" style="left:434px;width:330px" role="img" aria-label="Open living area toward the kitchen"></div>
  <div class="room" style="left:795px;width:337px" role="img" aria-label="Living room with television and ottoman"></div>
</section>

<section class="explore">
  <div class="eyebrow" style="left:74px;top:70px">EXPLORE BEND<span class="rule"></span></div>
  <h2 class="h2" style="left:74px;top:94px;font-size:44px;line-height:52px">Adventure, Dining<br>and More - Right<br>Nearby</h2>
  <p class="lead" style="left:74px;top:268px;width:300px;font-size:10px">From riverside trails and scenic walks to local breweries, restaurants, shopping, and live music, Bend offers something for every kind of getaway. Explore the outdoors, discover local favorites, or simply enjoy the relaxed charm of the city – all just minutes from your door.</p>
  <div class="btn btn-maroon" style="left:74px;top:384px;width:134px;height:36px">Book direct →</div>
  <div class="abs explore-list">
    <div class="explore-item"><span class="ic"></span>Hiking &amp; Biking Trails</div>
    <div class="explore-item"><span class="ic"></span>Restaurants &amp; Breweries</div>
    <div class="explore-item"><span class="ic"></span>Shopping &amp; Boutiques</div>
    <div class="explore-item"><span class="ic"></span>Live Music &amp; Events</div>
    <div class="explore-item"><span class="ic"></span>Parks &amp; Recreation</div>
  </div>
  <div class="abs serif" style="left:822px;top:56px;font-size:26px">Where you’ll be</div>
  <div class="abs" style="left:822px;top:100px;font-size:11px;color:var(--maroon);display:flex;gap:6px;align-items:center"><svg width="10" height="12" viewBox="0 0 10 12" fill="none" stroke="#7b0f15"><path d="M5 11S1 7 1 4.5a4 4 0 0 1 8 0C9 7 5 11 5 11z"/><circle cx="5" cy="4.5" r="1.3"/></svg>Bend, Oregon, United States</div>
  <div class="photo map" role="img" aria-label="Street map of Bend with the property marked"></div>
  <div class="abs" style="left:920px;top:262px;width:26px;height:26px;border-radius:50%;background:#e0245e;border:3px solid #fff"></div>
</section>

<section class="reviews">
  <div class="abs script" style="left:0;width:1200px;text-align:center;top:40px;font-size:30px">Guest Love</div>
  <h2 class="h2" style="left:0;width:1200px;text-align:center;top:80px;font-size:42px">What our guests are saying</h2>

  <article class="review" style="left:74px;width:239px"><div class="quote">“</div><div class="avatar" role="img" aria-label="Guest portrait"></div><div class="rev-name">Maren</div><div class="rev-sub">5 years on Staynest</div><div class="rev-stars stars">★★★★★</div><p class="rev-body">Very cute place central to Tannery Row. The water fountain in the back was very peaceful and we enjoyed our stay. Thank you!</p><div class="rev-more">Show more</div></article>
  <article class="review" style="left:343px;width:239px"><div class="quote">“</div><div class="avatar" role="img" aria-label="Guest portrait"></div><div class="rev-name">Delphine</div><div class="rev-sub">Beaverton, Oregon</div><div class="rev-stars stars">★★★★★</div><p class="rev-body">Great house in Bend, charming and very clean. Quiet neighborhood — we enjoyed our stay here. Ample parking. Well equipped kitchen. Bathrooms had extra amenities that..</p><div class="rev-more">Show more</div></article>
  <article class="review" style="left:610px;width:247px"><div class="quote">“</div><div class="avatar" role="img" aria-label="Guest portrait"></div><div class="rev-name">Tess</div><div class="rev-sub">6 years on Staynest</div><div class="rev-stars stars">★★★★★</div><p class="rev-body">This place is amazing and the personal touches were over the top! Rhonda was so kind and communicative. Great location, great house and we will definitely be back!</p><div class="rev-more">Show more</div></article>
  <article class="review score-card abs">
    <div style="width:34px;height:34px;border-radius:50%;background:#f1d9cf;margin:14px auto 6px"></div>
    <div style="font-size:13px;font-weight:600;color:var(--maroon)">Staynest Prime Keeper</div>
    <div style="font-size:32px;margin-top:8px">4.98<span style="color:#999;font-size:28px">/5</span></div>
    <div class="stars" style="font-size:24px">★★★★★</div>
    <div style="font-size:12px;font-weight:600;margin-top:14px">200+ Reviews</div>
    <div style="font-size:12px;margin-top:4px"><b>Top 1%</b> of Eligible Homes</div>
    <div class="btn btn-maroon" style="left:22px;top:246px;width:190px;height:40px">Read more reviews</div>
  </article>
  <div class="dots" style="left:470px;top:503px"><span class="on"></span><span></span><span></span></div>
</section>

<section class="booking">
  <div class="photo booking-bg" role="img" aria-label="Sunset over Central Oregon high desert and mountains"></div>
  <h2 class="h2" style="left:70px;top:74px;font-size:44px;line-height:48px;color:#fff">Ready to Plan<br>Your Bend Getaway?</h2>
  <p class="abs" style="left:70px;top:196px;font-size:13px;color:#eee">Book direct for the best rates and experience.</p>
  <div class="perk" style="left:70px;top:232px"><i></i>Best Rate Guarantee</div>
  <div class="perk" style="left:280px;top:232px"><i></i>Secure Payment with Paywell</div>
  <div class="perk" style="left:70px;top:268px"><i></i>Instant Confirmation</div>
  <div class="perk" style="left:280px;top:268px"><i></i>Easy Direct Booking</div>
  <form class="abs booking-form">
    <div class="f-label" style="left:32px;top:26px">FULL NAME</div><div class="f-input" style="left:32px;top:46px;width:226px">ex.join</div>
    <div class="f-label" style="left:288px;top:26px">EMAIL ADDRESS</div><div class="f-input" style="left:288px;top:46px;width:222px">ex.join@.com</div>
    <div class="f-label" style="left:32px;top:108px">CHECK-IN</div><div class="f-input" style="left:32px;top:128px;width:226px">Add date<span>▦</span></div>
    <div class="f-label" style="left:288px;top:108px">CHECK-OUT</div><div class="f-input" style="left:288px;top:128px;width:222px">Add date<span>▦</span></div>
    <div class="f-label" style="left:32px;top:188px">ADULTS</div><div class="f-input" style="left:32px;top:208px;width:116px">1 Guest<span>⌄</span></div>
    <div class="f-label" style="left:160px;top:188px">CHILDREN</div><div class="f-input" style="left:160px;top:208px;width:116px">1 Guest<span>⌄</span></div>
    <div class="f-label" style="left:288px;top:188px">PHONE</div><div class="f-input" style="left:288px;top:208px;width:222px">ex-1800-250-450</div>
    <div class="btn btn-maroon" style="left:32px;top:270px;width:478px;height:38px">Check availability →</div>
    <p class="abs" style="left:32px;top:322px;width:478px;text-align:center;font-size:11px">You’ll see nightly rates, cleaning fee, taxes and total before you pay.</p>
  </form>
</section>

<section class="pets">
  <div class="photo" role="img" aria-label="Golden retriever on a forest trail" style="left:74px;top:64px;width:298px;height:278px;border-radius:6px;background:linear-gradient(180deg,#6d7a45,#a08858 55%,#c8a070)"></div>
  <h2 class="h2" style="left:410px;top:60px;font-size:42px;line-height:52px">Bringing Your Best<br>Friend?</h2>
  <div class="abs" style="left:410px;top:176px;font-size:26px;font-weight:500;color:var(--maroon)">They're Welcome Too.</div>
  <p class="lead" style="left:410px;top:226px;width:320px;font-size:11px">Enjoy our private, fenced backyard and pet-friendly accommodations. Because great vacations are better together.</p>
  <div class="photo" role="img" aria-label="Illustration of a dog and cat" style="left:805px;top:96px;width:150px;height:140px;border-radius:50%;background:radial-gradient(circle at 60% 40%,#f6c33a 55%,#fff 56%)"></div>
  <div class="abs pet-list">
    <div><span class="tick"><svg width="10" height="8" viewBox="0 0 10 8"><path d="M1 4l3 3 5-6" stroke="#fff" fill="none" stroke-width="1.6"/></svg></span>Pet friendly</div>
    <div><span class="tick"><svg width="10" height="8" viewBox="0 0 10 8"><path d="M1 4l3 3 5-6" stroke="#fff" fill="none" stroke-width="1.6"/></svg></span>Fenced backyard<br>Nearby trails</div>
    <div><span class="tick"><svg width="10" height="8" viewBox="0 0 10 8"><path d="M1 4l3 3 5-6" stroke="#fff" fill="none" stroke-width="1.6"/></svg></span>Pets stay free</div>
  </div>
</section>

<section class="features">
  <div class="feat" style="left:96px"><span class="ic"></span><div><h4>Prime location</h4><p>Walk to the Tannery Row Quarter for shops, restaurants and the river.</p></div></div>
  <div class="feat" style="left:350px"><span class="ic"></span><div><h4>Guest favorite</h4><p>Top 1% of eligible Staynest homes with 4.98 stars and 200+ reviews.</p></div></div>
  <div class="feat" style="left:608px"><span class="ic"></span><div><h4>Outdoor paradise</h4><p>Minutes to hiking, biking, skiing, breweries and endless recreation.</p></div></div>
  <div class="feat" style="left:864px"><span class="ic"></span><div><h4>Book direct &amp; save</h4><p>No service fees. Secure online booking with instant confirmation.</p></div></div>
</section>

<section class="cta">
  <div class="photo cta-photo" role="img" aria-label="House exterior with blue sky"></div>
  <h2 class="h2" style="left:228px;top:48px;font-size:32px;color:#fff">Your Bend Getaway Starts Here</h2>
  <p class="abs" style="left:232px;top:102px;font-size:12px;color:#f1e6e6">Book Birch Lantern Retreat for an unforgettable stay in Central Oregon.</p>
  <div class="btn btn-outline" style="left:805px;top:65px;width:130px;height:38px">Book direct</div>
  <div class="btn" style="left:955px;top:65px;width:175px;height:38px;border:1px solid #fff;color:#fff">Check availability</div>
</section>

<footer class="site-footer">
  <div class="abs" style="left:102px;top:58px;width:46px;height:46px;border-radius:50%;background:var(--maroon)"></div>
  <div class="abs" style="left:160px;top:60px;font-size:20px;color:#fff">Birch Lantern Retreat</div>
  <div class="abs" style="left:161px;top:88px;font-size:9px">BEND, OREGON</div>
  <p class="abs" style="left:100px;top:124px;width:270px;font-size:11px;line-height:20px">Your home away from home in Bend. Walk Explore, Relax, Repeat.</p>
  <div class="social" style="left:98px" aria-label="Social profile"></div>
  <div class="social" style="left:150px" aria-label="Social profile"></div>
  <div class="social" style="left:202px" aria-label="Social profile"></div>

  <div class="f-head" style="left:530px">QUICK LINKS</div>
  <div class="f-links" style="left:530px">Home<br>The House<br>Gallery<br>Explore Bend</div>
  <div class="f-head" style="left:718px">POLICIES</div>
  <div class="f-links" style="left:718px">Pet Policy<br>Cancilation Policy<br>House Rules<br>Privacy Policy</div>
  <div class="f-head" style="left:895px">HAVE QUESTIONS?</div>
  <div class="f-links" style="left:895px">
    <div class="contact-row"><svg width="14" height="14" viewBox="0 0 14 14" fill="none" stroke="#ddd"><path d="M3 1h2l1 3-1.5 1a7 7 0 0 0 4 4L9.5 8l3 1v2a2 2 0 0 1-2 2A10 10 0 0 1 1 3a2 2 0 0 1 2-2z"/></svg>(541) 555-0187</div>
    <div class="contact-row"><svg width="14" height="12" viewBox="0 0 14 12" fill="none" stroke="#ddd"><rect x="1" y="1" width="12" height="10" rx="1"/><path d="M1 2l6 5 6-5"/></svg>hello@birchlanternretreat.com</div>
    <div class="contact-row"><svg width="12" height="14" viewBox="0 0 12 14" fill="none" stroke="#ddd"><path d="M6 13S1 8 1 5a5 5 0 0 1 10 0c0 3-5 8-5 8z"/><circle cx="6" cy="5" r="1.6"/></svg>Bend, Oregon, USA</div>
  </div>
  <div class="btn btn-maroon" style="left:895px;top:234px;width:130px;height:36px">Contact us →</div>
  <div class="abs" style="left:98px;top:296px;width:1010px;height:1px;background:#333"></div>
  <div class="abs" style="left:98px;top:316px;font-size:11px">© 2026 Birch Lantern Retreat. All rights reserved.</div>
  <div class="abs" style="left:938px;top:316px;font-size:11px">Privacy Policy | Terms of Use</div>
</footer>

</body>
</html>
```